Boutique Store Selling Antiques and Unique Finds

I need a Web Page designed for my Store Called "Willow Lane". I would like a very classic, muted design that looks European when pulled up. I will be selling Antiques from all over the world and Unique finds that have reproduced. I will also be selling high-end purses and jewelry with unique, reasonable products for the every-day buyer as well.

Target Market(s)

25-70 year old men and women;)

Coding

Coded - Design and coding required

Number of Pages Required

1 page

Colors

Designer to choose only greyscale colors for use in the design.

Requirements
Must have
• I want it

```html
<!DOCTYPE html>
<html lang="en">
<head>
<meta charset="utf-8">
<title>Willow Lane — Antiques and Unique Finds</title>
<link href="https://fonts.googleapis.com/css2?family=Jost:wght@400;500;600;700&display=swap" rel="stylesheet">
<style>
:root{
  --ink:#1c1c1c;
  --muted:#555;
  --white:#fff;
  --hero-top:#ededed;
  --hero-bottom:#e1e1e1;
  --soft:#f4f4f4;
  --paper:#f0f0f0;
  --accent:#d2d2d2;
  --accent-line:#6a6a6a;
  --line:#8a8a8a;
  --black:#000;
  --shadow:0 3px 10px rgba(0,0,0,.14);
}
*{box-sizing:border-box;margin:0;padding:0}
html,body{width:1200px;height:4163px;overflow:hidden}
body{position:relative;background:var(--white);font-family:"Jost",Arial,sans-serif;color:var(--ink)}
.abs{position:absolute}
.photo{position:absolute}
/* header + hero */
.hero{position:absolute;left:0;top:0;width:1200px;height:734px;background:linear-gradient(180deg,var(--hero-top),var(--hero-bottom))}
.nav a{position:absolute;top:74px;font-size:14px;font-weight:600;color:var(--ink);text-decoration:none;letter-spacing:.3px}
.nav .active::after{content:"";position:absolute;left:-4px;right:-4px;top:30px;height:2px;background:var(--ink)}
.logo{position:absolute;left:0;width:1200px;text-align:center;font-weight:500;letter-spacing:7px;color:var(--ink)}
.logo-mark{display:block;margin:0 auto 8px;width:16px;height:16px;background:var(--ink)}
.util{position:absolute;top:22px;font-size:13px;font-weight:600;display:flex;align-items:center;gap:6px}
.arrow{position:absolute;top:350px}
.btn{position:absolute;background:var(--accent);color:var(--ink);font-weight:600;display:flex;align-items:center;justify-content:center;letter-spacing:.4px}
.dots{position:absolute;top:688px;left:562px;display:flex;gap:10px}
.dots span{width:14px;height:14px;border-radius:50%;background:var(--white)}
.dots .on{background:#2a2a2a}
/* section titles */
.title{position:absolute;left:0;width:1200px;text-align:center;font-weight:600;font-size:37px;letter-spacing:5px}
/* product cards */
.card{position:absolute;background:var(--white);box-shadow:var(--shadow);padding:14px 20px 0}
.card.hot{background:var(--accent)}
.card .name{text-align:center;font-weight:500;font-size:17px;letter-spacing:1.2px}
.card .row{display:flex;align-items:center;margin-top:14px;gap:12px}
.card .price{margin-left:auto;font-weight:600;font-size:25px}
.ico{width:34px;height:34px;border-radius:50%;border:1px solid #999;display:flex;align-items:center;justify-content:center}
.hot .ico{border-color:var(--accent-line)}
/* shop online */
.shop{position:absolute;left:0;top:1692px;width:1200px;height:648px;background:var(--paper)}
.tile{position:absolute;border:1px solid var(--line);background:var(--white)}
.tile .cap{position:absolute;left:0;right:0;bottom:0;height:95px;text-align:center;padding-top:30px;font-size:13px;font-weight:600;letter-spacing:.8px}
.tile .cap small{display:block;font-weight:400;font-size:13px;margin-top:4px;letter-spacing:0}
.pop{position:absolute;height:76px;background:var(--soft);display:flex;align-items:center;justify-content:space-between;padding:0 24px 0 33px;font-weight:600;font-size:20px;letter-spacing:1.1px}
/* about */
.about{position:absolute;left:609px;top:2897px;width:582px;height:375px;background:var(--soft);text-align:center}
.about h2{margin-top:98px;font-size:30px;font-weight:600;letter-spacing:3.5px}
.about p{width:400px;margin:22px auto 0;font-size:12px;line-height:22px;color:#333}
/* newsletter */
.news h2{position:absolute;left:0;width:1200px;top:3345px;text-align:center;font-size:32px;font-weight:600;letter-spacing:4px;line-height:38px}
.field{position:absolute;left:394px;width:428px;height:47px;border:1.5px solid #777;font-size:12px;padding:0 24px;display:flex;align-items:center;color:#444}
/* footer */
.footer{position:absolute;left:0;top:3714px;width:1200px;height:449px;background:var(--black);color:var(--white)}
.fcol{position:absolute;top:170px;font-size:12px;line-height:25.5px}
.fcol h3{font-size:16px;font-weight:400;letter-spacing:.5px;line-height:22px;margin-bottom:2px}
.frule{position:absolute;left:0;right:0;top:386px;height:1px;background:#333}
.fbot{position:absolute;top:403px;font-size:9px;color:#aaa}
</style>
</head>
<body>

<header class="hero">
  <div class="util" style="left:874px"><svg width="20" height="22" viewBox="0 0 20 22" fill="none" stroke="#1c1c1c" stroke-width="1.6"><circle cx="10" cy="7" r="5"/><path d="M2 21c0-5 4-8 8-8s8 3 8 8"/></svg>MY ACCOUNT</div>
  <div class="util" style="left:1023px"><svg width="22" height="20" viewBox="0 0 22 20" fill="none" stroke="#1c1c1c" stroke-width="1.6"><path d="M2 7h18l-2 11H4z"/><path d="M7 7l4-5 4 5"/></svg>BASKET</div>
  <nav class="nav">
    <a class="active" href="#" style="left:95px">HOME</a>
    <a href="#" style="left:187px">SHOP ONLINE</a>
    <a href="#" style="left:333px">PRODUCTS</a>
    <a href="#" style="left:806px">DISCOVER</a>
    <a href="#" style="left:925px">BLOGS</a>
    <a href="#" style="left:1020px">CONTACT US</a>
  </nav>
  <div class="logo" style="top:36px;font-size:24px"><span class="logo-mark"></span>WILLOW LANE</div>
  <div class="photo" role="img" aria-label="Gilded antique crown resting on a stack of old leather-bound books" style="left:362px;top:153px;width:500px;height:422px;background:radial-gradient(ellipse at 50% 35%,#a9874a,#6b4f2c 55%,#3a2a1e 90%);border-radius:6px"></div>
  <svg class="arrow" style="left:72px" width="30" height="58" viewBox="0 0 30 58" fill="none" stroke="#444" stroke-width="3"><path d="M27 2L3 29l24 27"/></svg>
  <svg class="arrow" style="left:1090px" width="30" height="58" viewBox="0 0 30 58" fill="none" stroke="#444" stroke-width="3"><path d="M3 2l24 27L3 56"/></svg>
  <div class="btn" style="left:510px;top:603px;width:170px;height:43px;font-size:15px">LEARN MORE</div>
  <div class="dots"><span></span><span class="on"></span><span></span></div>
</header>

<h2 class="title" style="top:805px">OUR PRODUCTS</h2>

<div class="photo" role="img" aria-label="Antique steel helmet on art books" style="left:94px;top:924px;width:320px;height:247px;background:linear-gradient(160deg,#7d7a72,#3b3a37)"></div>
<div class="photo" role="img" aria-label="Gilded crown on old books" style="left:418px;top:897px;width:359px;height:274px;background:linear-gradient(160deg,#b7ada0,#7c6640 60%,#4a3a2a)"></div>
<div class="photo" role="img" aria-label="Carved stone bust in a wood-panelled hall" style="left:785px;top:924px;width:319px;height:247px;background:linear-gradient(150deg,#5a321e,#c7b8a0 60%,#6b4a30)"></div>
<div class="photo" role="img" aria-label="Fur-trimmed jewelled crown on a book" style="left:94px;top:1288px;width:320px;height:244px;background:linear-gradient(160deg,#b3aca3,#2a2420 60%,#5b5750)"></div>
<div class="photo" role="img" aria-label="Ornate gold crown with blue stones" style="left:438px;top:1288px;width:320px;height:244px;background:linear-gradient(160deg,#3a3630,#9c8a6a 55%,#2c2a28)"></div>
<div class="photo" role="img" aria-label="Antique medal on a blue ribbon" style="left:785px;top:1288px;width:319px;height:244px;background:linear-gradient(160deg,#ddd4c5,#b9ad98 60%,#cfc4b2)"></div>

<div class="card" style="left:105px;top:1136px;width:297px;height:108px"><div class="name">Product Name</div><div class="row"><span class="ico"><svg width="16" height="14" viewBox="0 0 16 14" fill="none" stroke="#555" stroke-width="1.4"><path d="M8 13L2 7a3.3 3.3 0 016-4 3.3 3.3 0 016 4z"/></svg></span><span class="ico"><svg width="14" height="12" viewBox="0 0 14 12" fill="#444"><path d="M0 0h3l1 2h10l-2 6H5z"/><circle cx="5" cy="10.5" r="1.3"/><circle cx="11" cy="10.5" r="1.3"/></svg></span><span class="price">$55.00</span></div></div>
<div class="card hot" style="left:431px;top:1136px;width:333px;height:116px"><div class="name" style="font-size:18px;font-weight:600">Product Name</div><div class="row"><span class="ico"><svg width="16" height="14" viewBox="0 0 16 14" fill="none" stroke="#444" stroke-width="1.4"><path d="M8 13L2 7a3.3 3.3 0 016-4 3.3 3.3 0 016 4z"/></svg></span><span class="ico"><svg width="14" height="12" viewBox="0 0 14 12" fill="#333"><path d="M0 0h3l1 2h10l-2 6H5z"/><circle cx="5" cy="10.5" r="1.3"/><circle cx="11" cy="10.5" r="1.3"/></svg></span><span class="price">$60.00</span></div></div>
<svg class="abs" style="left:711px;top:1160px" width="16" height="22" viewBox="0 0 16 22"><path d="M1 1v18l5-5 4 7 3-1-4-7h6z" fill="#111" stroke="#fff"/></svg>
<div class="card" style="left:796px;top:1136px;width:297px;height:108px"><div class="name">Product Name</div><div class="row"><span class="ico"><svg width="16" height="14" viewBox="0 0 16 14" fill="none" stroke="#555" stroke-width="1.4"><path d="M8 13L2 7a3.3 3.3 0 016-4 3.3 3.3 0 016 4z"/></svg></span><span class="ico"><svg width="14" height="12" viewBox="0 0 14 12" fill="#444"><path d="M0 0h3l1 2h10l-2 6H5z"/><circle cx="5" cy="10.5" r="1.3"/><circle cx="11" cy="10.5" r="1.3"/></svg></span><span class="price">$35.00</span></div></div>
<div class="card" style="left:105px;top:1498px;width:297px;height:106px"><div class="name">Product Name</div><div class="row"><span class="ico"><svg width="16" height="14" viewBox="0 0 16 14" fill="none" stroke="#555" stroke-width="1.4"><path d="M8 13L2 7a3.3 3.3 0 016-4 3.3 3.3 0 016 4z"/></svg></span><span class="ico"><svg width="14" height="12" viewBox="0 0 14 12" fill="#444"><path d="M0 0h3l1 2h10l-2 6H5z"/><circle cx="5" cy="10.5" r="1.3"/><circle cx="11" cy="10.5" r="1.3"/></svg></span><span class="price">$55.00</span></div></div>
<div class="card" style="left:450px;top:1498px;width:297px;height:106px"><div class="name">Product Name</div><div class="row"><span class="ico"><svg width="16" height="14" viewBox="0 0 16 14" fill="none" stroke="#555" stroke-width="1.4"><path d="M8 13L2 7a3.3 3.3 0 016-4 3.3 3.3 0 016 4z"/></svg></span><span class="ico"><svg width="14" height="12" viewBox="0 0 14 12" fill="#444"><path d="M0 0h3l1 2h10l-2 6H5z"/><circle cx="5" cy="10.5" r="1.3"/><circle cx="11" cy="10.5" r="1.3"/></svg></span><span class="price">$35.00</span></div></div>
<div class="card" style="left:796px;top:1498px;width:297px;height:106px"><div class="name">Product Name</div><div class="row"><span class="ico"><svg width="16" height="14" viewBox="0 0 16 14" fill="none" stroke="#555" stroke-width="1.4"><path d="M8 13L2 7a3.3 3.3 0 016-4 3.3 3.3 0 016 4z"/></svg></span><span class="ico"><svg width="14" height="12" viewBox="0 0 14 12" fill="#444"><path d="M0 0h3l1 2h10l-2 6H5z"/><circle cx="5" cy="10.5" r="1.3"/><circle cx="11" cy="10.5" r="1.3"/></svg></span><span class="price">$33.00</span></div></div>

<section class="shop">
  <h2 class="title" style="top:56px">SHOP ONLINE</h2>
  <div class="tile" style="left:94px;top:139px;width:496px;height:402px">
    <div class="photo" role="img" aria-label="Drawer of vintage fabrics, ribbons and trims" style="left:0;top:0;width:494px;height:307px;background:linear-gradient(140deg,#9a8a6a,#3b3833 45%,#c8c2b6 70%,#2b2d33)"></div>
    <div class="cap">MURANO CARAFE GOLD SWIRL<small>$1,350.00</small></div>
  </div>
  <div class="tile" style="left:611px;top:139px;width:496px;height:402px">
    <div class="photo" role="img" aria-label="Dark gilded frame around a damask panel" style="left:0;top:0;width:494px;height:307px;background:linear-gradient(90deg,#d6ccb8,#3a2e22 15%,#d9cfbc 28%,#e3dac8 72%,#3a2e22 85%,#d6ccb8)"></div>
    <div class="cap">MURANO CARAFE GOLD SWIRL<small>$1,350.00</small></div>
  </div>
</section>

<h2 class="title" style="top:2396px">POPULAR&nbsp;&nbsp;ITEMS</h2>
<div class="photo" role="img" aria-label="Close view of a carved gilt antique frame" style="left:103px;top:2479px;width:492px;height:286px;background:linear-gradient(130deg,#4e4c48,#6d5a3a 50%,#2e261c)"></div>
<div class="pop" style="left:103px;top:2765px;width:492px"><span>PRODUCT ANTIQUE FRAME</span><span>$1,350.00</span></div>
<div class="photo" role="img" aria-label="Dark gilded frame around a damask panel" style="left:624px;top:2479px;width:491px;height:286px;background:linear-gradient(90deg,#d6ccb8,#3a2e22 15%,#d9cfbc 28%,#e3dac8 72%,#3a2e22 85%,#d6ccb8)"></div>
<div class="pop" style="left:624px;top:2765px;width:491px"><span>PRODUCT ANTIQUE FRAME</span><span>$150.00</span></div>

<div class="photo" role="img" aria-label="Antique steel helmet standing on art books" style="left:0;top:2897px;width:609px;height:375px;background:radial-gradient(ellipse at 40% 40%,#8e8b84,#4a4844 50%,#2a2a2a)"></div>
<section class="about">
  <h2>ABOUT US WILLOW LANE</h2>
  <p>Lorem Ipsum is simply dummy text of the printing and typesetting industry. Lorem Ipsum has been the industry's standard dummy text ever since the 1500s, when an unknown printer.</p>
  <div class="btn" style="left:218px;top:248px;width:146px;height:37px;font-size:12px">LEARN MORE</div>
</section>

<section class="news">
  <h2>SIGN UP FOR OUR NEWSLETTER<br>TO STAY UPDATED</h2>
  <div class="field" style="top:3450px">Your Name</div>
  <div class="field" style="top:3512px">Your Email address</div>
  <div class="btn" style="left:391px;top:3575px;width:433px;height:48px;font-size:15px;letter-spacing:2px">SUBSCRIBE NOW</div>
</section>

<footer class="footer">
  <div class="logo" style="top:28px;font-size:23px;color:var(--white)"><span class="logo-mark" style="background:var(--white)"></span>WILLOW LANE</div>
  <div class="fcol" style="left:162px"><h3>ABOUT US</h3>A Family Business<br>Philosophy and Ethos<br>Charity and Community<br>Press<br>Careers</div>
  <div class="fcol" style="left:425px"><h3>SPECIAL EVENTS</h3>Workshops<br>Private Events Richmond<br>Private Events Covent Garden<br>Supper Clubs</div>
  <div class="fcol" style="left:734px"><h3>RESOURCES</h3>Terms and Conditions<br>Privacy Policy<br>Contact</div>
  <div class="fcol" style="left:983px"><h3>SOCIAL</h3>Instagram<br>Facebook<br>Pinterest<br>Twitter</div>
  <div class="frule"></div>
  <div class="fbot" style="left:178px">2021 © Willow Lane &nbsp;|&nbsp; All Right Reserved</div>
  <div class="fbot" style="left:882px">Cookies &nbsp;&nbsp;&nbsp; Sitemap &nbsp;&nbsp;&nbsp; Terms of Use</div>
</footer>

</body>
</html>
```